Existing Website Requiring new Pages

I have an existing word press website that was built using elementor.
Website: www.tallowcrestcare.com.au
I require the Vacancies page (https://www.tallowcrestcare.com.au/vacancies/) to be modified to display our new properties along with minor tweaks to how the information is presented.
The vacancies to be displayed are the exactly the same as those that are located on the homepage of QMR website (https://qmr.org.au/)
The new pages that link off the Vacancies tab will require custom design.
There are roughly 8 pages/properties to be incorporated. i wish for the design to be very similar to that displayed in the following link; https://www.polunda.com.au/vacancies/merrylands
Along with this the back end has not been updated for the last 3 years so it also requires some maintenance.
Website is in the disability industry and the custom pages will display information relative to Property Vacancies.
I have attached a ZIP file with some design guides, the information for each of the properties (which will need to be modified to show our business name Tallowcrest Care) and the example of how it is to look based off the Polunda website.
If you guys have any suggestions or ideas on how to make this more presentable or possible i'm open to your ideas.
Target Market(s)
People looking for SDA properties custom built for people with a disability
Industry/Entity Type
Disability
Coding
Coded - Design and coding required
Number of Pages Required
5+ page

```html
<!DOCTYPE html>
<html lang="en">
<head>
<meta charset="utf-8">
<title>Vacancies | Tallowcrest Care</title>
<link href="https://fonts.googleapis.com/css2?family=Montserrat:wght@700&family=Roboto:wght@400;500&display=swap" rel="stylesheet">
<style>
:root{
  --ink:#141414;
  --muted:#4a4a4a;
  --teal:#22c3a6;
  --orange:#f5a94a;
  --pink:#e0439a;
  --line:#e3e3e3;
  --footer:#f4f4f4;
  --bar:#262626;
  --white:#ffffff;
}
*{box-sizing:border-box;margin:0;padding:0}
html,body{width:819px;height:1200px;overflow:hidden}
body{font-family:"Roboto",sans-serif;color:var(--ink);background:var(--white);position:relative}

/* Header */
.site-header{position:absolute;top:0;left:0;width:819px;height:74px;background:var(--white);z-index:2}
.brand-tab{position:absolute;left:77px;top:0;width:130px;height:94px;background:var(--white);
  clip-path:polygon(0 0,100% 0,100% 78%,88% 100%,12% 100%,0 78%);display:flex;flex-direction:column;align-items:center;justify-content:center;gap:5px;z-index:3}
.brand-mark{width:22px;height:22px;border-radius:50%;background:var(--pink)}
.brand-name{font-size:11px;font-weight:500;color:var(--ink);letter-spacing:.4px}
.social{position:absolute;top:9px;left:457px;display:flex;gap:5px}
.social span{width:24px;height:24px;border-radius:50%;display:block}
.s1{background:#3a5a99}.s2{background:#6a2a7a}.s3{background:#e2467d}.s4{background:#1f74b5}
.header-divider{position:absolute;left:587px;top:11px;width:1px;height:20px;background:var(--line)}
.call{position:absolute;left:606px;top:9px;display:flex;align-items:center;gap:6px}
.call-icon{width:25px;height:25px;border-radius:50%;background:var(--teal);display:flex;align-items:center;justify-content:center}
.call-label{font-size:7.5px;color:var(--muted);display:block}
.call-number{font-size:10.5px;font-weight:500;color:var(--teal);display:block;margin-top:1px}
.main-nav{position:absolute;top:51px;left:257px;display:flex;font-size:9px;font-weight:500}
.main-nav a{color:var(--ink);text-decoration:none;position:absolute;white-space:nowrap}
.main-nav a.current{color:var(--orange)}

/* Hero */
.hero{position:absolute;top:74px;left:0;width:819px;height:328px;
  background:linear-gradient(90deg,#6e5a50 0%,#8a7a70 35%,#a08c6e 55%,#7c7a78 75%,#4e4c4a 100%)}
.hero::after{content:"";position:absolute;inset:0;background:linear-gradient(90deg,rgba(0,0,0,.35),rgba(0,0,0,0) 55%)}
.hero-text{position:absolute;left:98px;top:100px;z-index:1;color:var(--white)}
.hero-title{font-family:"Montserrat",sans-serif;font-weight:700;font-size:33px;line-height:1}
.hero-lead{margin-top:14px;font-size:10.5px;line-height:22px;font-weight:500;width:210px}

/* Listings */
.listings{position:absolute;left:93px;width:632px;display:grid;grid-template-columns:repeat(4,150px);column-gap:11px}
.row-1{top:456px}.row-2{top:712px}
.section-rule{position:absolute;left:0;top:688px;width:819px;height:1px;background:#cfcfcf}
.property{background:var(--white);height:211px;box-shadow:0 1px 6px rgba(0,0,0,.06)}
.property.is-active{box-shadow:0 4px 14px rgba(0,0,0,.14)}
.property-photo{height:132px}
.property-name{font-size:11.5px;font-weight:500;padding:15px 13px 8px;border-bottom:1px solid var(--line);margin:0 4px 0 4px;padding-left:9px}
.is-active .property-name{color:var(--orange);border-color:var(--orange)}
.property-type{display:flex;align-items:center;gap:6px;padding:10px 13px;font-size:9.3px;color:var(--muted)}
.ph-a{background:linear-gradient(180deg,#c9d6e6 0%,#9a8f86 55%,#5f7a45 100%)}
.ph-b{background:linear-gradient(180deg,#8ec2ea 0%,#a86a55 45%,#5f8e3a 75%,#b07565 100%)}
.ph-c{background:linear-gradient(180deg,#69b3e6 0%,#e4d9bc 55%,#7ca04a 100%)}
.ph-d{background:linear-gradient(180deg,#8fbde0 0%,#e3d2b8 45%,#6ea23c 100%)}
.ph-e{background:linear-gradient(180deg,#9fcdf0 0%,#cdbaa0 50%,#4aa43a 100%)}
.ph-f{background:linear-gradient(180deg,#8fc4ee 0%,#c77444 45%,#aab0a8 100%)}
.ph-g{background:linear-gradient(180deg,#5aa4e0 0%,#a5533e 45%,#4c7e34 100%)}
.ph-h{background:linear-gradient(180deg,#5aa8e8 0%,#9aa7b5 45%,#5c9c35 100%)}

/* Footer */
.site-footer{position:absolute;top:979px;left:0;width:819px;height:189px;background:var(--footer)}
.footer-brand{position:absolute;left:98px;top:32px;display:flex;flex-direction:column;gap:10px}
.footer-brand .brand-row{display:flex;align-items:center;gap:6px}
.footer-brand .brand-mark{width:28px;height:28px}
.footer-brand .brand-name{font-size:13px}
.footer-social{display:flex;gap:5px;margin-top:54px}
.footer-social span{width:21px;height:21px;border-radius:50%;display:block}
.footer-col{position:absolute;top:45px}
.footer-col h3{font-size:10.5px;font-weight:500;letter-spacing:.2px;margin-bottom:9px}
.footer-col li{list-style:none;font-size:7.4px;color:var(--muted);height:17.5px}
.col-accom{left:245px}.col-services{left:433px}.col-contact{left:587px}
.contact-item{display:flex;gap:6px;margin-bottom:9px}
.contact-item b{display:block;font-size:8px;font-weight:500;margin-bottom:4px}
.contact-item span{font-size:7.4px;color:var(--muted)}
.copyright{position:absolute;top:1168px;left:0;width:819px;height:32px;background:var(--bar);color:var(--white);
  font-size:8.5px;display:flex;align-items:center;justify-content:center}
</style>
</head>
<body>

<header class="site-header">
  <div class="brand-tab">
    <span class="brand-mark"></span>
    <span class="brand-name">Tallowcrest Care</span>
  </div>
  <div class="social" aria-label="Social links">
    <span class="s1"></span><span class="s2"></span><span class="s3"></span><span class="s4"></span>
  </div>
  <div class="header-divider"></div>
  <div class="call">
    <div class="call-icon">
      <svg width="12" height="12" viewBox="0 0 24 24" fill="#fff"><path d="M6.6 10.8a15 15 0 0 0 6.6 6.6l2.2-2.2a1 1 0 0 1 1-.25 11.4 11.4 0 0 0 3.6.57 1 1 0 0 1 1 1V20a1 1 0 0 1-1 1A17 17 0 0 1 3 4a1 1 0 0 1 1-1h3.5a1 1 0 0 1 1 1c0 1.25.2 2.45.57 3.6a1 1 0 0 1-.25 1z"/></svg>
    </div>
    <div>
      <span class="call-label">24 Hour Call</span>
      <span class="call-number">61 0400 118 362</span>
    </div>
  </div>
  <nav class="main-nav">
    <a style="left:0">HOME</a>
    <a style="left:60px">ABOUT US</a>
    <a class="current" style="left:138px">WHAT WE DO &#8964;</a>
    <a style="left:240px">REFERRALS</a>
    <a style="left:325px">FEEDBACK</a>
    <a style="left:405px">CONTACT US</a>
  </nav>
</header>

<section class="hero" role="img" aria-label="Photo of a smiling woman in a wheelchair working on a laptop at a wooden table in a brick-walled room">
  <div class="hero-text">
    <h1 class="hero-title">Vacancies</h1>
    <p class="hero-lead">Tallowcrest Care is a Sydney based disability support services provider.</p>
  </div>
</section>

<svg width="0" height="0" style="position:absolute">
  <symbol id="bed" viewBox="0 0 24 16"><g fill="none" stroke="#22c3a6" stroke-width="1.3"><rect x="2" y="1" width="20" height="9" rx="1"/><rect x="5" y="4" width="6" height="3" rx="1"/><rect x="13" y="4" width="6" height="3" rx="1"/><path d="M1 10h22v4H1zM2 14v2M22 14v2"/></g></symbol>
</svg>

<section class="listings row-1">
  <article class="property"><div class="property-photo ph-a" role="img" aria-label="Photo of a single-storey home in Penrith"></div><h2 class="property-name">Penrith</h2><p class="property-type"><svg width="15" height="10"><use href="#bed"/></svg>4 Bedroom SIL Home</p></article>
  <article class="property"><div class="property-photo ph-b" role="img" aria-label="Photo of a brick home in Mount Druitt"></div><h2 class="property-name">Mount Druitt</h2><p class="property-type"><svg width="15" height="10"><use href="#bed"/></svg>4 Bedroom SIL Home</p></article>
  <article class="property is-active"><div class="property-photo ph-c" role="img" aria-label="Photo of a rendered home in Casula"></div><h2 class="property-name">Casula</h2><p class="property-type"><svg width="15" height="10"><use href="#bed"/></svg>4 Bedroom SIL Home</p></article>
  <article class="property"><div class="property-photo ph-d" role="img" aria-label="Photo of a period cottage in Eastwood"></div><h2 class="property-name">Eastwood</h2><p class="property-type"><svg width="15" height="10"><use href="#bed"/></svg>4 Bedroom SIL Home</p></article>
</section>

<div class="section-rule"></div>

<section class="listings row-2">
  <article class="property"><div class="property-photo ph-e" role="img" aria-label="Photo of a brick home with palm tree in Baulkham Hills"></div><h2 class="property-name">Baulkham Hills</h2><p class="property-type"><svg width="15" height="10"><use href="#bed"/></svg>4 Bedroom SIL Home</p></article>
  <article class="property"><div class="property-photo ph-f" role="img" aria-label="Photo of a brick home with driveway in Merrylands"></div><h2 class="property-name">Merrylands</h2><p class="property-type"><svg width="15" height="10"><use href="#bed"/></svg>4 Bedroom SIL Home</p></article>
  <article class="property"><div class="property-photo ph-g" role="img" aria-label="Photo of a two-storey brick house"></div><h2 class="property-name">Lorem Ipsum</h2><p class="property-type"><svg width="15" height="10"><use href="#bed"/></svg>4 Bedroom SIL Home</p></article>
  <article class="property"><div class="property-photo ph-h" role="img" aria-label="Photo of a weatherboard house with front garden"></div><h2 class="property-name">Lorem Ipsum</h2><p class="property-type"><svg width="15" height="10"><use href="#bed"/></svg>4 Bedroom SIL Home</p></article>
</section>

<footer class="site-footer">
  <div class="footer-brand">
    <div class="brand-row"><span class="brand-mark"></span><span class="brand-name">Tallowcrest Care</span></div>
    <div class="footer-social"><span class="s1"></span><span class="s2"></span><span class="s3"></span><span class="s4"></span></div>
  </div>
  <div class="footer-col col-accom">
    <h3>ACCOMMODATION</h3>
    <ul><li>Supported Independent Living (SIL)</li><li>Specialist Disability Accommodation (SDA)</li><li>Short term Accommodation (Respite)</li><li>Vacancies</li></ul>
  </div>
  <div class="footer-col col-services">
    <h3>WHAT WE DO</h3>
    <ul><li>In Home Care</li><li>Social &amp; Community Services</li><li>Therapeutic Supports</li><li>Support Coordination</li><li>Home Modifications</li></ul>
  </div>
  <div class="footer-col col-contact">
    <h3>CONTACT US</h3>
    <div class="contact-item"><svg width="9" height="9" viewBox="0 0 24 24"><circle cx="12" cy="12" r="10" fill="none" stroke="#e0439a" stroke-width="2.5"/><path d="M12 6v6l4 2" stroke="#e0439a" stroke-width="2.5" fill="none"/></svg><div><b>Operating Hours</b><span>9AM To 5PM Monday - Friday</span></div></div>
    <div class="contact-item"><svg width="9" height="9" viewBox="0 0 24 24" fill="#e0439a"><path d="M6.6 10.8a15 15 0 0 0 6.6 6.6l2.2-2.2a1 1 0 0 1 1-.25 11.4 11.4 0 0 0 3.6.57 1 1 0 0 1 1 1V20a1 1 0 0 1-1 1A17 17 0 0 1 3 4a1 1 0 0 1 1-1h3.5a1 1 0 0 1 1 1c0 1.25.2 2.45.57 3.6a1 1 0 0 1-.25 1z"/></svg><div><b>Phone</b><span>+61 0400 118 362</span></div></div>
    <div class="contact-item"><svg width="9" height="9" viewBox="0 0 24 24" fill="#e0439a"><path d="M2 5h20v14H2z"/><path d="M2 5l10 8 10-8" stroke="#fff" stroke-width="2" fill="none"/></svg><div><b>Email:</b><span>info@tallowcrestcare.com.au</span></div></div>
  </div>
</footer>

<div class="copyright">© Copyright 2024 | Tallowcrest Care | All Rights Reserved.</div>

</body>
</html>
```